Visitenkarten-Design für Sonnen-/Fensterschutz
Zielgruppe
KLW GmbH ist eine Firma, die Sonnenschutz und Fensterschutz anbieten.
'Ihr kompetenter Partner in Sachen Sonnenschutz- , Fenster- und Türtechnik. Sie erhalten echtes Handwerk aus dem Mühlviertel zu fairen Preisen.'
Unsere Zielgruppe sind Personen mit Haus, die am Land leben.
Firmenname: KLW GmbH
Slogan: Fenster & Sonnenschutz
Aufgabenstellung
Hier befindet sich das Logodesign: https://dx.qv/t-QwLpo7RbNs
Bitte ein schlichtes Design bereitstellen mit einer Dummy-Person:
Jonas Weidlinger + Telefonnummer + Email
Die finalen Daten bitte erst am Schluss berücksichtigen (für Gewinnerdesign)
Gerne auch hintern + vorne bedruckbar bereitstellen.

```html
<!DOCTYPE html>
<html lang="de">
<head>
<meta charset="utf-8">
<title>KLW GmbH – Visitenkarte</title>
<link rel="stylesheet" href="https://fonts.googleapis.com/css2?family=Open+Sans:wght@400;600&family=Poppins:wght@500;600&display=swap">
<style>
  :root {
    --stage: #262626;
    --card-dark: #3a3a3a;
    --orange: #e0762a;
    --red: #c9352a;
    --dark-red: #8e1f1d;
    --text-light: #e9e9e9;
    --text-muted: #bdbdbd;
    --white: #ffffff;
  }
  * { margin: 0; padding: 0; box-sizing: border-box; }
  html, body { width: 1200px; height: 801px; overflow: hidden; }
  body {
    background: var(--stage);
    font-family: "Open Sans", Arial, sans-serif;
    position: relative;
  }
  .card {
    position: absolute;
    width: 520px;
    height: 300px;
    border-radius: 6px;
    overflow: hidden;
    box-shadow: 0 10px 30px rgba(0,0,0,.45);
  }
  .card--front { left: 70px; top: 90px; background: var(--card-dark); }
  .card--back {
    left: 70px; top: 430px;
    background: linear-gradient(160deg, var(--orange) 0%, var(--red) 45%, var(--red) 100%);
    display: flex; align-items: center; justify-content: center;
  }

  .brand { display: flex; align-items: center; gap: 12px; }
  .brand__mark { width: 22px; height: 22px; background: var(--orange); }
  .brand__name {
    font-family: "Poppins", Arial, sans-serif;
    font-weight: 600;
    color: var(--orange);
    letter-spacing: 1px;
  }
  .brand__slogan {
    font-family: "Poppins", Arial, sans-serif;
    font-weight: 500;
    color: var(--dark-red);
    text-transform: uppercase;
    letter-spacing: 1px;
  }

  .card--front .brand { position: absolute; left: 36px; top: 34px; }
  .card--front .brand__name { font-size: 34px; line-height: 1; }
  .card--front .brand__slogan {
    position: absolute; left: 70px; top: 80px; font-size: 12px; color: var(--red);
  }

  .contact {
    position: absolute; left: 300px; top: 112px;
    color: var(--text-light); font-size: 11px; line-height: 1.55;
  }
  .contact__company { font-weight: 600; font-size: 13px; margin-bottom: 2px; }
  .contact__row { display: flex; align-items: center; gap: 8px; }
  .contact__row svg { width: 12px; height: 12px; flex: none; }

  .person { position: absolute; left: 36px; top: 196px; color: var(--text-light); }
  .person__name { font-size: 19px; }
  .person__role { font-size: 12px; color: var(--text-muted); margin-top: 2px; }

  .stripes { position: absolute; right: 0; bottom: 0; width: 260px; height: 170px; }

  .card--back .brand { flex-direction: column; gap: 10px; }
  .card--back .brand__mark { width: 28px; height: 28px; background: var(--white); }
  .card--back .brand__name { color: var(--white); font-size: 56px; line-height: 1; }

  .lockup {
    position: absolute; left: 690px; top: 330px;
  }
  .lockup .brand__mark { width: 36px; height: 36px; background: var(--orange); }
  .lockup .brand__name { font-size: 84px; line-height: 1; }
  .lockup .brand__rule { height: 2px; background: var(--dark-red); margin: 10px 0 6px; }
  .lockup .brand__slogan { font-size: 24px; }
</style>
</head>
<body>

  <section class="card card--front" aria-label="Visitenkarte Vorderseite">
    <div class="brand">
      <span class="brand__mark"></span>
      <span class="brand__name">KLW GmbH</span>
    </div>
    <div class="brand__slogan">Fenster &amp; Sonnenschutz</div>

    <div class="contact">
      <div class="contact__company">KLW GmbH</div>
      <div class="contact__row">
        <svg viewBox="0 0 12 12"><path d="M6 1a3.5 3.5 0 0 0-3.5 3.5C2.5 7.3 6 11 6 11s3.5-3.7 3.5-6.5A3.5 3.5 0 0 0 6 1zm0 5a1.5 1.5 0 1 1 0-3 1.5 1.5 0 0 1 0 3z" fill="#c9352a"/></svg>
        <span>Am Lindenhang 7, 4020 Linz</span>
      </div>
      <div class="contact__row">
        <svg viewBox="0 0 12 12"><path d="M3 1l2 2.5-1 1.2a6 6 0 0 0 3.3 3.3l1.2-1L11 9l-1 2C5 11 1 7 1 2z" fill="#c9352a"/></svg>
        <span>+49 170 482 1936</span>
      </div>
      <div class="contact__row">
        <svg viewBox="0 0 12 12"><rect x="1" y="2.5" width="10" height="7" fill="#c9352a"/><path d="M1 2.5l5 4 5-4" stroke="#3a3a3a" stroke-width="1" fill="none"/></svg>
        <span>+49 170 482 1936</span>
      </div>
    </div>

    <div class="person">
      <div class="person__name">Jonas Weidlinger</div>
      <div class="person__role">Geschäftsführer</div>
    </div>

    <svg class="stripes" viewBox="0 0 260 170" aria-hidden="true">
      <defs>
        <linearGradient id="stripe-grad" x1="0" y1="1" x2="1" y2="0">
          <stop offset="0" stop-color="#c9352a"/>
          <stop offset="1" stop-color="#e0762a"/>
        </linearGradient>
      </defs>
      <polygon points="60,170 260,20 260,32 76,170" fill="url(#stripe-grad)"/>
      <polygon points="92,170 260,44 260,62 116,170" fill="url(#stripe-grad)"/>
      <polygon points="132,170 260,74 260,84 145,170" fill="url(#stripe-grad)"/>
      <polygon points="158,170 260,94 260,100 166,170" fill="url(#stripe-grad)"/>
    </svg>
  </section>

  <section class="card card--back" aria-label="Visitenkarte Rückseite">
    <div class="brand">
      <span class="brand__mark"></span>
      <span class="brand__name">KLW GmbH</span>
    </div>
  </section>

  <section class="lockup" aria-label="Firmenname">
    <div class="brand">
      <span class="brand__mark"></span>
      <span class="brand__name">KLW GmbH</span>
    </div>
    <div class="brand__rule"></div>
    <div class="brand__slogan">Fenster &amp; Sonnenschutz</div>
  </section>

</body>
</html>
```